Brackwell Yard Services Flyer Design

I need a new flyer design for my business, Brackwell Yard Services. I’ll be providing my old flyer and logo as references. The new flyer should feature updated wording, contact information, logos, and photos, but still keep the original “What We Do” section and include the phrase “Don’t See? Just Ask!” somewhere near the services. The flyer needs to look great in black and white for door-to-door handouts but also be eye-catching and professional enough for social media use.

The updated content should include the headline “Transforming Outdoor Spaces with Hard Work & Precision” and highlight three main service areas: Landscaping Services (project-based landscaping to clean, prepare, and transform outdoor spaces with precision), Property Cleanup (quick hauls, debris removal, or full cleanouts—no job too big or small), and Ground Preparation (pad preparation, brush removal, and fire lines—making properties safe, functional, and project-ready).

Please also include a “Why Choose Us?” section that lists: Locally owned since 2022, Reliable & affordable – no corners cut, Professional results you can trust, LICENSED AND Insured, and Quality work / on time / references / flexible / follow-up.

At the bottom, include the contact details: Call or Text Today!
www.brackwellyard.example
| sales@brackwellyard.example
| (555) 014-7293

The overall design should be clean, professional, and easy to read with a layout that clearly shows what we offer. Use visuals that represent outdoor services, landscaping, and property cleanup/prep work. I want something that feels trustworthy, family-friendly, and modern.
Use the same photo of leaf clean up from the original flyer if possible.
Our company colors are also black and white. For the most part.

```html
<!DOCTYPE html>
<html lang="en">
<head>
<meta charset="utf-8">
<title>Brackwell Yard Services Flyer</title>
<link rel="stylesheet" href="https://fonts.googleapis.com/css2?family=Bebas+Neue&family=Oswald:wght@600;700&family=Source+Sans+3:wght@400;600;700&display=swap">
<style>
  :root {
    --orange: #f7941d;
    --white: #ffffff;
    --ink: #1c1c1c;
    --black: #000000;
    --rule: #f4a04a;
  }
  * { box-sizing: border-box; margin: 0; padding: 0; }
  html, body { width: 927px; height: 1200px; overflow: hidden; background: var(--white); }
  .flyer { position: relative; width: 927px; height: 1200px; overflow: hidden; background: var(--white); font-family: "Source Sans 3", sans-serif; color: var(--ink); }

  .header-band { position: absolute; left: 0; top: 0; width: 927px; height: 100px; }
  .headline { position: absolute; left: 28px; top: 12px; width: 470px; text-align: center; font-family: "Oswald", sans-serif; font-weight: 700; font-size: 33px; line-height: 35px; color: var(--white); text-transform: uppercase; letter-spacing: 0.2px; }
  .brand { position: absolute; right: 22px; top: 22px; display: flex; align-items: center; gap: 8px; }
  .brand-mark { width: 34px; height: 34px; background: var(--white); border-radius: 50%; }
  .brand-name { font-family: "Oswald", sans-serif; font-weight: 700; font-size: 21px; line-height: 22px; color: var(--white); text-transform: uppercase; width: 170px; }

  .photo { position: absolute; top: 104px; height: 305px; }
  .photo-cleanup { left: 3px; width: 299px; background: linear-gradient(160deg, #4a4f47 0%, #6b6357 45%, #8a7a62 70%, #3e3a33 100%); }
  .photo-leaves { left: 311px; width: 304px; background: linear-gradient(180deg, #4b5446 0%, #5a5d4c 45%, #9a7550 75%, #7a5a3d 100%); }
  .photo-saw { left: 624px; width: 298px; background: linear-gradient(170deg, #56605a 0%, #4a4640 45%, #6a5c4a 75%, #3a3530 100%); }

  .tag { position: absolute; height: 48px; background: var(--orange); color: var(--white); font-family: "Source Sans 3", sans-serif; font-weight: 700; font-size: 34px; line-height: 48px; padding-left: 10px; letter-spacing: -0.5px; }
  .tag-services { left: 37px; top: 431px; width: 200px; }
  .tag-why { left: 37px; top: 859px; width: 269px; padding-left: 16px; }
  .tag-what { left: 608px; top: 431px; width: 198px; padding-left: 12px; }

  .section-head { position: absolute; font-family: "Bebas Neue", sans-serif; font-size: 32px; line-height: 32px; color: var(--orange); white-space: nowrap; }
  .service-copy { position: absolute; left: 42px; width: 460px; font-size: 16.5px; line-height: 22px; color: var(--ink); }

  .bullet-list { position: absolute; list-style: none; }
  .bullet-list li { position: relative; padding-left: 26px; font-size: 17px; line-height: 30.3px; height: 30.3px; white-space: nowrap; }
  .bullet-list li::before { content: ""; position: absolute; left: 0; top: 8px; width: 18px; height: 15px; background: var(--orange); clip-path: polygon(25% 0, 75% 0, 100% 50%, 75% 100%, 25% 100%, 0 50%); }

  .divider { position: absolute; left: 553px; top: 453px; width: 1.5px; height: 615px; background: var(--rule); }

  .licensed { position: absolute; left: 40px; top: 1050px; width: 475px; text-align: center; font-family: "Bebas Neue", sans-serif; font-size: 28px; line-height: 28px; color: var(--orange); }
  .qualities { position: absolute; left: 40px; top: 1080px; width: 475px; text-align: center; font-size: 16.5px; line-height: 22px; white-space: nowrap; }
  .qualities .dot { display: inline-block; width: 6px; height: 6px; border-radius: 50%; background: var(--orange); vertical-align: middle; margin: 0 4px 3px; }

  .footer { position: absolute; left: 0; top: 1108px; width: 927px; height: 92px; }
  .cta { position: absolute; left: 0; top: 1123px; width: 927px; text-align: center; font-family: "Oswald", sans-serif; font-weight: 700; font-size: 30px; line-height: 36px; color: var(--orange); text-transform: uppercase; }
  .contact-row { position: absolute; left: 0; top: 1163px; width: 927px; display: flex; justify-content: center; gap: 22px; align-items: center; }
  .contact-item { display: flex; align-items: center; gap: 7px; font-weight: 700; font-size: 19.5px; line-height: 24px; color: var(--orange); white-space: nowrap; }
  .contact-item svg { flex: none; }
</style>
</head>
<body>
<main class="flyer">

  <svg class="header-band" viewBox="0 0 927 100" aria-hidden="true">
    <polygon fill="#f7941d" points="0,0 927,0 927,94 900,96 870,93 830,97 790,94 740,96 700,93 650,97 600,94 560,96 520,93 470,97 420,94 380,96 330,93 290,97 240,94 200,96 160,93 110,97 70,94 30,96 0,93"/>
  </svg>
  <h1 class="headline">Transforming Outdoor Spaces<br>with Hard Work &amp; Precision</h1>
  <div class="brand">
    <span class="brand-mark"></span>
    <span class="brand-name">Brackwell Yard Services</span>
  </div>

  <div class="photo photo-cleanup" role="img" aria-label="Worker pushing a wheelbarrow loaded with cut branches along a gravel drive"></div>
  <div class="photo photo-leaves" role="img" aria-label="Worker raking a pile of autumn leaves on a lawn"></div>
  <div class="photo photo-saw" role="img" aria-label="Worker in a hard hat cutting a fallen tree limb with a chainsaw"></div>

  <h2 class="tag tag-services">Our Services</h2>

  <h3 class="section-head" style="left:41px; top:500px;">Landscaping Services</h3>
  <p class="service-copy" style="top:548px;">Project-based landscaping to clean, prepare, and transform outdoor spaces with precision.</p>

  <h3 class="section-head" style="left:41px; top:617px;">Ground Preparation</h3>
  <p class="service-copy" style="top:664px;">Pad preparation, brush removal, and fire lines—making properties safe, functional, and project-ready.</p>

  <h3 class="section-head" style="left:41px; top:733px;">Property Cleanup</h3>
  <p class="service-copy" style="top:781px;">Quick hauls, debris removal, or full cleanouts—no job too big or small.</p>

  <h2 class="tag tag-why">Why Choose Us?</h2>
  <ul class="bullet-list" style="left:41px; top:921px;">
    <li>Locally owned since 2022</li>
    <li>Reliable &amp; affordable – no corners cut</li>
    <li>Professional results you can trust</li>
  </ul>

  <p class="licensed">Licensed and Insured</p>
  <p class="qualities">Quality work<span class="dot"></span>On Time<span class="dot"></span>References<span class="dot"></span>Flexible<span class="dot"></span>Follow-up</p>

  <div class="divider"></div>

  <h2 class="tag tag-what">What We Do</h2>

  <h3 class="section-head" style="left:612px; top:500px;">Remove</h3>
  <ul class="bullet-list" style="left:613px; top:542px;">
    <li>Junk removal</li>
    <li>Trash &amp; waste hauling</li>
    <li>Yard &amp; garden cleanup</li>
    <li>Appliance removal</li>
  </ul>

  <h3 class="section-head" style="left:610px; top:686px;">Install</h3>
  <ul class="bullet-list" style="left:611px; top:727px;">
    <li>Mulch</li>
    <li>DG</li>
    <li>Plants</li>
    <li>Rock</li>
  </ul>

  <h3 class="section-head" style="left:610px; top:871px;">Maintenance &amp; Other</h3>
  <ul class="bullet-list" style="left:611px; top:913px;">
    <li>Yard cleanup</li>
    <li>Weed prevention (pre-emergent)</li>
    <li>Roof &amp; gutter cleaning</li>
    <li>Fence &amp; deck staining</li>
  </ul>

  <p class="section-head" style="left:610px; top:1051px; font-size:28px;">Don’t See? Just Ask!</p>

  <svg class="footer" viewBox="0 0 927 92" aria-hidden="true">
    <polygon fill="#000000" points="0,6 40,3 90,7 140,2 200,6 260,3 320,7 380,2 440,6 500,3 560,7 620,2 680,6 740,3 800,7 860,2 927,5 927,92 0,92"/>
  </svg>
  <p class="cta">Call or Text Today!</p>
  <div class="contact-row">
    <span class="contact-item">
      <svg width="24" height="24" viewBox="0 0 24 24" fill="none" stroke="#f7941d" stroke-width="1.4" aria-hidden="true"><circle cx="12" cy="12" r="10.5"/><ellipse cx="12" cy="12" rx="4.5" ry="10.5"/><line x1="1.5" y1="12" x2="22.5" y2="12"/><path d="M3.5 6.5h17M3.5 17.5h17"/></svg>
      www.brackwellyard.example
    </span>
    <span class="contact-item">
      <svg width="26" height="20" viewBox="0 0 26 20" fill="none" stroke="#f7941d" stroke-width="1.4" aria-hidden="true"><rect x="1" y="1" width="24" height="18"/><path d="M1 1l12 10 12-10M1 19l9-8M25 19l-9-8"/></svg>
      sales@brackwellyard.example
    </span>
    <span class="contact-item">
      <svg width="22" height="22" viewBox="0 0 24 24" fill="none" stroke="#f7941d" stroke-width="1.4" aria-hidden="true"><path d="M6.5 2.5l3 4.5-2 2.2c1.2 2.8 3.6 5.2 6.3 6.3l2.2-2 4.5 3-1.8 3.4C12 19.5 4.5 12 4.1 4.3z"/></svg>
      (555) 014-7293
    </span>
  </div>

</main>
</body>
</html>
```